Website design for luxury private hair salon

I'm looking for someone to use my Logo and build me a website for my webpage www.corsetresses.com.au (You can have a look at it as it has every detail I need included on it already), however I want a fresh new appearance and it to look and feel super stylish.

I am thinking colours in black, with silver or white, beautiful hair images like the ones you'll see on the current webpage - the price list as per what you already see.

I will include a copy of my biz card on here, so you can see the feel of the card, and design a website with a similar feel. It is matt black with a foil silver.

Modern, but classic and fresh. I will also need you to be able to publish it to my URL for me as I have no idea how to do this. I need it up and running pronto!

The website will need to be able to be read clearly on all devices incluing smart phones and ipads. The URL is currently registered and hosted by Norvel Web

Thinking a Home Page - large logo etc and write up on who and what we offer
Services/Price List page - as per the price list on my current webpage
Contact Page - with a built in contact form.

Target Market(s)

Middle aged, fashionable, stylish women and men who enjoy luxury hair care and styling in an upmarket location.

Industry/Entity Type

Hair And Beauty

Number of Pages Required

3 page

Font styles to use
Other font styles liked:
• see my images for my current logo

Colors
000000
b2b2b2
a54499

Requirements
Must have
• Style
• Fast turnaround
• Be viewable on all devices, PC, ipads, smart phones
• Designer able to upload it so its a running website for me to my URL
Nice to have
• Just a really feminine, stylish website which is easy to read and shows some beautiful images of perfect hair
Should not have
• Browns, reds or orange colours.

```html
<!DOCTYPE html>
<html lang="en">
<head>
<meta charset="utf-8">
<title>Corsetresses hair &amp; body — Price List</title>
<link rel="stylesheet" href="https://fonts.googleapis.com/css2?family=Montserrat:ital,wght@0,300;0,400;0,500;0,600;1,400&display=swap">
<style>
:root{
  --night:#0d0b2e;
  --night-deep:#07061c;
  --silver:#9aa0a8;
  --ink:#2f2f2f;
  --text:#3a3a3a;
  --muted:#8a8a8a;
  --rule:#e2e2e2;
  --footer:#1e1e1e;
  --white:#ffffff;
  --plum:#a54499;
}
*{box-sizing:border-box;margin:0;padding:0}
html,body{width:702px;height:1200px;overflow:hidden;background:var(--white)}
body{position:relative;font-family:"Montserrat",Arial,sans-serif;color:var(--text)}

.hero{position:absolute;left:0;top:0;width:702px;height:396px;
  background:radial-gradient(ellipse at 25% 50%,#1c1a4a 0%,var(--night) 45%,var(--night-deep) 100%);overflow:hidden}
.hero-photo{position:absolute;right:0;top:0;width:420px;height:396px;
  background:radial-gradient(ellipse at 62% 45%,rgba(214,176,140,.55) 0%,rgba(150,110,80,.35) 35%,rgba(13,11,46,0) 72%)}
.main-nav{position:absolute;top:13px;left:0;width:702px;display:flex;justify-content:center;gap:32px}
.main-nav a{color:var(--white);text-decoration:none;font-size:9px;font-weight:600;letter-spacing:.5px}
.main-nav a.is-faded{color:#cfd0dc}
.nav-rule{position:absolute;top:36px;left:45px;width:612px;height:1px;background:rgba(255,255,255,.12)}
.brand-hero{position:absolute;left:46px;top:150px;color:var(--silver)}
.brand-hero .brand-name{font-size:52px;font-weight:300;letter-spacing:1px;line-height:1}
.brand-hero .brand-tag{margin:14px 0 0 116px;font-size:26px;font-weight:300;letter-spacing:2px}

.model-photo{position:absolute;left:0;top:470px;width:332px;height:596px;
  background:linear-gradient(180deg,#f6f1ea 0%,#efe6dc 40%,#f4f4f4 100%)}

.price-title{position:absolute;left:257px;top:424px;font-size:26px;font-weight:300;color:var(--ink)}
.price-intro{position:absolute;left:256px;top:464px;font-family:Arial,Helvetica,sans-serif;font-size:11.5px;color:#222}

.price-table{position:absolute;left:255px;top:490px;width:402px;border-collapse:collapse;table-layout:fixed;border:1px solid var(--rule)}
.price-table thead th{height:34px;background:var(--ink);color:#c9c9c9;font-weight:400;font-size:12.5px}
.price-table td{height:30.85px;border-top:1px solid var(--rule);font-size:9.5px;font-weight:500;color:#3d3d3d}
.price-table .service{padding-left:18px;text-align:left;white-space:nowrap}
.price-table .rate{text-align:center}
.price-table .rate-principal{padding-left:24px}
.price-table .book{text-align:center;border-left:1px solid var(--rule)}
.price-table thead .book-head{border-left:1px solid #555}
.price-table col.c-service{width:160px}
.price-table col.c-apprentice{width:80px}
.price-table col.c-principal{width:106px}
.price-table col.c-book{width:56px}
.cal{width:12px;height:12px;vertical-align:middle}
.cal rect,.cal line{stroke:#8a8a8a}
.is-active .cal rect,.is-active .cal line{stroke:#111}

.price-notes{position:absolute;left:255px;top:962px;width:402px;text-align:center;font-family:Arial,Helvetica,sans-serif;font-size:7px;line-height:12.5px;color:#333}
.partner{position:absolute;font-weight:600}
.partner-prisma{left:348px;top:1003px;font-size:20px;color:var(--plum);letter-spacing:1px}
.partner-lumera{left:495px;top:998px;width:69px;height:37px;background:#111;color:var(--white);font-size:13px;display:flex;align-items:center;justify-content:center;letter-spacing:1px}

.site-footer{position:absolute;left:0;top:1066px;width:702px;height:134px;background:var(--footer)}
.footer-nav{position:absolute;left:77px;top:40px;display:flex;gap:20px}
.footer-nav a{color:#cfcfcf;text-decoration:none;font-size:8.5px;font-family:Arial,Helvetica,sans-serif}
.follow{position:absolute;left:77px;top:61px;display:flex;align-items:center;gap:8px;color:#cfcfcf;font-size:8.5px;font-family:Arial,Helvetica,sans-serif}
.follow .dot{width:25px;height:25px;border:1.5px solid #dcdcdc;border-radius:50%}
.brand-footer{position:absolute;left:258px;top:30px;width:128px;text-align:center;color:var(--silver)}
.brand-footer .brand-name{font-size:17px;font-weight:300;letter-spacing:.5px}
.brand-footer .brand-tag{font-size:9px;letter-spacing:1px;margin-top:6px}
.contact-mail{position:absolute;left:436px;top:44px;display:flex;align-items:center;gap:7px;font-size:7.5px;font-style:italic;color:#b8b8b8}
.copyright{position:absolute;left:438px;top:65px;font-size:7.5px;color:#b8b8b8}
.copyright .owner{color:#3a3a3a}
</style>
</head>
<body>

<header class="hero">
  <div class="hero-photo" role="img" aria-label="Photo of a woman with long glossy wavy blonde hair"></div>
  <nav class="main-nav">
    <a href="#">HOME</a>
    <a href="#" class="is-faded">SERVICES</a>
    <a href="#" class="is-faded">CONTACT</a>
  </nav>
  <div class="nav-rule"></div>
  <div class="brand-hero">
    <div class="brand-name">Corsetresses</div>
    <div class="brand-tag">hair &amp; body</div>
  </div>
</header>

<div class="model-photo" role="img" aria-label="Photo of a woman with flowing strawberry blonde hair in a white floral dress"></div>

<h1 class="price-title">Price List</h1>
<p class="price-intro">We use and recommend LUMERA and PRISMA hair colours and styling products</p>

<table class="price-table">
  <colgroup><col class="c-service"><col class="c-apprentice"><col class="c-principal"><col class="c-book"></colgroup>
  <thead>
    <tr><th></th><th>Apprentice</th><th class="rate-principal">Principal</th><th class="book-head"></th></tr>
  </thead>
  <tbody>
    <tr class="is-active"><td class="service">Styling</td><td class="rate">25</td><td class="rate rate-principal">40</td><td class="book"><svg class="cal" viewBox="0 0 12 12" fill="none" stroke-width="1.4"><rect x="1" y="2" width="10" height="9"/><line x1="1" y1="4.5" x2="11" y2="4.5"/><line x1="3.5" y1="0.5" x2="3.5" y2="2.5"/><line x1="8.5" y1="0.5" x2="8.5" y2="2.5"/></svg></td></tr>
    <tr><td class="service">Glide Curls</td><td class="rate">35</td><td class="rate rate-principal">50</td><td class="book"><svg class="cal" viewBox="0 0 12 12" fill="none" stroke-width="1"><rect x="1" y="2" width="10" height="9"/><line x1="1" y1="4.5" x2="11" y2="4.5"/><line x1="3.5" y1="0.5" x2="3.5" y2="2.5"/><line x1="8.5" y1="0.5" x2="8.5" y2="2.5"/></svg></td></tr>
    <tr><td class="service">Hair Up</td><td class="rate">35</td><td class="rate rate-principal">60</td><td class="book"><svg class="cal" viewBox="0 0 12 12" fill="none" stroke-width="1"><rect x="1" y="2" width="10" height="9"/><line x1="1" y1="4.5" x2="11" y2="4.5"/><line x1="3.5" y1="0.5" x2="3.5" y2="2.5"/><line x1="8.5" y1="0.5" x2="8.5" y2="2.5"/></svg></td></tr>
    <tr><td class="service">Ladies Cut</td><td class="rate">15</td><td class="rate rate-principal">30</td><td class="book"><svg class="cal" viewBox="0 0 12 12" fill="none" stroke-width="1"><rect x="1" y="2" width="10" height="9"/><line x1="1" y1="4.5" x2="11" y2="4.5"/><line x1="3.5" y1="0.5" x2="3.5" y2="2.5"/><line x1="8.5" y1="0.5" x2="8.5" y2="2.5"/></svg></td></tr>
    <tr><td class="service">Cut with Blow dry</td><td class="rate">25</td><td class="rate rate-principal">40</td><td class="book"><svg class="cal" viewBox="0 0 12 12" fill="none" stroke-width="1"><rect x="1" y="2" width="10" height="9"/><line x1="1" y1="4.5" x2="11" y2="4.5"/><line x1="3.5" y1="0.5" x2="3.5" y2="2.5"/><line x1="8.5" y1="0.5" x2="8.5" y2="2.5"/></svg></td></tr>
    <tr><td class="service">Restyle &amp; Finish</td><td class="rate">30</td><td class="rate rate-principal">50</td><td class="book"><svg class="cal" viewBox="0 0 12 12" fill="none" stroke-width="1"><rect x="1" y="2" width="10" height="9"/><line x1="1" y1="4.5" x2="11" y2="4.5"/><line x1="3.5" y1="0.5" x2="3.5" y2="2.5"/><line x1="8.5" y1="0.5" x2="8.5" y2="2.5"/></svg></td></tr>
    <tr><td class="service">Kids / Mens Cut</td><td class="rate">10</td><td class="rate rate-principal">20</td><td class="book"><svg class="cal" viewBox="0 0 12 12" fill="none" stroke-width="1"><rect x="1" y="2" width="10" height="9"/><line x1="1" y1="4.5" x2="11" y2="4.5"/><line x1="3.5" y1="0.5" x2="3.5" y2="2.5"/><line x1="8.5" y1="0.5" x2="8.5" y2="2.5"/></svg></td></tr>
    <tr><td class="service">Colour - Roots</td><td class="rate">30</td><td class="rate rate-principal">50</td><td class="book"><svg class="cal" viewBox="0 0 12 12" fill="none" stroke-width="1"><rect x="1" y="2" width="10" height="9"/><line x1="1" y1="4.5" x2="11" y2="4.5"/><line x1="3.5" y1="0.5" x2="3.5" y2="2.5"/><line x1="8.5" y1="0.5" x2="8.5" y2="2.5"/></svg></td></tr>
    <tr><td class="service">Extra Tint or Toner</td><td class="rate">20</td><td class="rate rate-principal">20</td><td class="book"><svg class="cal" viewBox="0 0 12 12" fill="none" stroke-width="1"><rect x="1" y="2" width="10" height="9"/><line x1="1" y1="4.5" x2="11" y2="4.5"/><line x1="3.5" y1="0.5" x2="3.5" y2="2.5"/><line x1="8.5" y1="0.5" x2="8.5" y2="2.5"/></svg></td></tr>
    <tr><td class="service">Add Foils 1/4 Head</td><td class="rate">20</td><td class="rate rate-principal">30</td><td class="book"><svg class="cal" viewBox="0 0 12 12" fill="none" stroke-width="1"><rect x="1" y="2" width="10" height="9"/><line x1="1" y1="4.5" x2="11" y2="4.5"/><line x1="3.5" y1="0.5" x2="3.5" y2="2.5"/><line x1="8.5" y1="0.5" x2="8.5" y2="2.5"/></svg></td></tr>
    <tr><td class="service">Add Foils 1/2 Head</td><td class="rate">40</td><td class="rate rate-principal">60</td><td class="book"><svg class="cal" viewBox="0 0 12 12" fill="none" stroke-width="1"><rect x="1" y="2" width="10" height="9"/><line x1="1" y1="4.5" x2="11" y2="4.5"/><line x1="3.5" y1="0.5" x2="3.5" y2="2.5"/><line x1="8.5" y1="0.5" x2="8.5" y2="2.5"/></svg></td></tr>
    <tr><td class="service">Full Head Foils</td><td class="rate">70</td><td class="rate rate-principal">90</td><td class="book"><svg class="cal" viewBox="0 0 12 12" fill="none" stroke-width="1"><rect x="1" y="2" width="10" height="9"/><line x1="1" y1="4.5" x2="11" y2="4.5"/><line x1="3.5" y1="0.5" x2="3.5" y2="2.5"/><line x1="8.5" y1="0.5" x2="8.5" y2="2.5"/></svg></td></tr>
    <tr><td class="service">Perm with Cut</td><td class="rate">60</td><td class="rate rate-principal">80</td><td class="book"><svg class="cal" viewBox="0 0 12 12" fill="none" stroke-width="1"><rect x="1" y="2" width="10" height="9"/><line x1="1" y1="4.5" x2="11" y2="4.5"/><line x1="3.5" y1="0.5" x2="3.5" y2="2.5"/><line x1="8.5" y1="0.5" x2="8.5" y2="2.5"/></svg></td></tr>
    <tr><td class="service">Permanenr Straightening</td><td class="rate">80</td><td class="rate rate-principal">120</td><td class="book"><svg class="cal" viewBox="0 0 12 12" fill="none" stroke-width="1"><rect x="1" y="2" width="10" height="9"/><line x1="1" y1="4.5" x2="11" y2="4.5"/><line x1="3.5" y1="0.5" x2="3.5" y2="2.5"/><line x1="8.5" y1="0.5" x2="8.5" y2="2.5"/></svg></td></tr>
  </tbody>
</table>

<p class="price-notes">ALL COLOURING INCLUDES A COMPLIMENTARY HAIR TREATMENT<br>TEA / COFFEE / WINE - ABSOLUTELY ON US!</p>
<div class="partner partner-prisma">PRISMA</div>
<div class="partner partner-lumera">LUMERA</div>

<footer class="site-footer">
  <nav class="footer-nav">
    <a href="#">HOME</a>
    <a href="#">SERVICES</a>
    <a href="#">CONTACT</a>
  </nav>
  <div class="follow">FOLLOW US <span class="dot"></span></div>
  <div class="brand-footer">
    <div class="brand-name">Corsetresses</div>
    <div class="brand-tag">hair &amp; body</div>
  </div>
  <div class="contact-mail">
    <svg width="9" height="7" viewBox="0 0 9 7"><rect x="0" y="0" width="9" height="7" fill="#8a8a8a"/><polyline points="0,0 4.5,4 9,0" fill="none" stroke="#1e1e1e" stroke-width="1"/></svg>
    hello@corsetresses.com.au
  </div>
  <div class="copyright">© <span class="owner">Corsetresses Hair</span> - 2016. All Rights Reserved.</div>
</footer>

</body>
</html>
```